Corvane Capital Business Cards

These are professional business cards that are for my family office.
Put fake emails and phone numbers as of now until I finalize those components. This family office controls my families investments, assets, and future. The cards should be professional.
..
.
.
.
I just uploaded another variation of a logo I would like to see as a business card to I am inbeteen which logo to use

Target Market(s)

business

Industry/Entity Type

business

Contact Information for Business Card

Professional, wealth related, finance related.

Requirements
Must have
• Logo

```html
<!DOCTYPE html>
<html lang="en">
<head>
<meta charset="utf-8">
<title>Corvane Capital Business Cards</title>
<link rel="stylesheet" href="https://fonts.googleapis.com/css2?family=Montserrat:wght@400;500&family=Open+Sans:wght@600&display=swap">
<style>
  :root {
    --backdrop: #d8d3ca;
    --card: #1b1f2b;
    --text-light: #ffffff;
    --text-soft: #e4e6ec;
    --name-grey: #b4b6bb;
    --ring: #ffffff;
    --ring-faint: #2c3754;
  }
  * { margin: 0; padding: 0; box-sizing: border-box; }
  html, body {
    width: 900px; height: 1200px; overflow: hidden;
    background: var(--backdrop);
  }
  .canvas { position: relative; width: 900px; height: 1200px; }
  .card {
    position: absolute;
    background: var(--card);
    border-radius: 24px;
    box-shadow: 0 10px 22px rgba(0,0,0,0.28);
    overflow: hidden;
  }
  .card-front { left: 80px; top: 132px; width: 742px; height: 440px; }
  .card-back  { left: 78px; top: 638px; width: 744px; height: 442px; }

  .brand-name {
    position: absolute;
    font-family: "Montserrat", sans-serif;
    font-weight: 500;
    color: var(--text-light);
    text-transform: uppercase;
    white-space: nowrap;
  }
  .card-front .brand-name {
    left: 36px; top: 66px;
    font-size: 31px; letter-spacing: 2px;
  }
  .holder { position: absolute; right: 47px; top: 50px; text-align: right; }
  .holder-name {
    font-family: "Open Sans", sans-serif; font-weight: 600;
    font-size: 27px; color: var(--name-grey); line-height: 1.2;
  }
  .holder-role {
    font-family: "Montserrat", sans-serif; font-weight: 400;
    font-size: 17px; color: var(--text-soft); line-height: 1.3;
  }
  .address {
    position: absolute; left: 38px; top: 268px;
    font-family: "Montserrat", sans-serif; font-size: 16px; font-style: normal;
    color: var(--text-soft); line-height: 20px;
  }
  .contact-list {
    position: absolute; left: 37px; top: 326px; list-style: none;
    font-family: "Montserrat", sans-serif; font-size: 16px; color: var(--text-soft);
  }
  .contact-list li { display: flex; align-items: center; height: 28.5px; }
  .contact-list svg { width: 15px; height: 15px; margin-right: 10px; fill: var(--text-soft); }

  .front-ring {
    position: absolute; left: 440px; top: 158px;
    width: 264px; height: 264px; border-radius: 50%;
    border: 5px solid var(--ring-faint);
    box-shadow: 0 3px 8px rgba(0,0,0,0.35);
  }
  .back-ring {
    position: absolute; left: 270px; top: 80px;
    width: 212px; height: 212px; border-radius: 50%;
    border: 5px solid var(--ring);
  }
  .card-back .brand-name {
    left: 0; right: 0; top: 318px; text-align: center;
    font-size: 38px; letter-spacing: 3px;
  }
</style>
</head>
<body>
<main class="canvas">
  <section class="card card-front" aria-label="Business card front">
    <div class="brand-name">Corvane Capital</div>
    <div class="holder">
      <div class="holder-name">Marcus Ellery</div>
      <div class="holder-role">Owner</div>
    </div>
    <address class="address">
      48 Harbor View Lane<br>Fairhaven, NJ 07704 USA
    </address>
    <ul class="contact-list">
      <li>
        <svg viewBox="0 0 24 24" aria-hidden="true"><path d="M6.6 10.8a15.1 15.1 0 0 0 6.6 6.6l2.2-2.2a1 1 0 0 1 1-.25 11.4 11.4 0 0 0 3.6.57 1 1 0 0 1 1 1V20a1 1 0 0 1-1 1A17 17 0 0 1 3 4a1 1 0 0 1 1-1h3.5a1 1 0 0 1 1 1c0 1.25.2 2.45.57 3.57a1 1 0 0 1-.25 1z"/></svg>
        (555)014-2870
      </li>
      <li>
        <svg viewBox="0 0 24 24" aria-hidden="true"><path d="M3 5h18a1 1 0 0 1 1 1v.5l-10 6.5L2 6.5V6a1 1 0 0 1 1-1zm-1 4 10 6.3L22 9v9a1 1 0 0 1-1 1H3a1 1 0 0 1-1-1z"/></svg>
        info@corvanecapital.com
      </li>
      <li>
        <svg viewBox="0 0 24 24" aria-hidden="true"><path d="M12 2a10 10 0 1 0 0 20 10 10 0 0 0 0-20zm-1 17.9A8 8 0 0 1 4.2 10.8L9 15.5v1a2 2 0 0 0 2 2zm6.9-2.5A2 2 0 0 0 16 16h-1v-3a1 1 0 0 0-1-1H8v-2h2a1 1 0 0 0 1-1V7h2a2 2 0 0 0 2-2v-.4a8 8 0 0 1 2.9 12.8z"/></svg>
        www.corvanecapital.com
      </li>
    </ul>
    <div class="front-ring" aria-hidden="true"></div>
  </section>

  <section class="card card-back" aria-label="Business card back">
    <div class="back-ring" aria-hidden="true"></div>
    <div class="brand-name">Corvane Capital</div>
  </section>
</main>
</body>
</html>
```